Inspirational Quotes Poster Set

Brookloft is a stylish coworking space, which has a design-oriented vintage look from the 60's with an industrial touch (www.brookloft-example.com) Brookloft Quote Poster Set of 16 posters. The poster should be typo oriented and rather simple. Reflecting a bit the clean billboard design from the sixties. Minimal / simple graphical elements

Target Market(s)

Startups and Entrepreneurs

Industry/Entity Type

Startup

Font styles to use
Sans Serif

Colors

Designer to choose colors to be used in the design.

Requirements
Must have
• Posters need to be on and very stylish

```html
<!DOCTYPE html>
<html lang="en">
<head>
<meta charset="utf-8">
<title>Brookloft Quote Poster Set</title>
<link rel="stylesheet" href="https://fonts.googleapis.com/css2?family=Space+Grotesk:wght@700&display=swap">
<style>
  :root {
    --poster-gold: #c9a20b;
    --ink-white: #ffffff;
  }
  html, body {
    margin: 0;
    padding: 0;
    overflow: hidden;
    background: var(--poster-gold);
  }
  .poster {
    position: relative;
    width: 801px;
    height: 1200px;
    background: var(--poster-gold);
    color: var(--ink-white);
    font-family: "Space Grotesk", Arial, sans-serif;
    font-weight: 700;
    overflow: hidden;
  }
  .quote {
    margin: 0;
    font-size: 96px;
    font-weight: 700;
  }
  .quote-line {
    position: absolute;
    left: 59px;
    width: 689px;
    display: flex;
    justify-content: space-between;
    line-height: 96px;
    height: 96px;
    letter-spacing: 12px;
  }
  .attribution {
    position: absolute;
    left: 70px;
    top: 1018px;
    margin: 0;
    font-size: 22px;
    line-height: 28px;
    letter-spacing: 0.5px;
  }
  .brand-name {
    position: absolute;
    left: 314px;
    top: 1104px;
    margin: 0;
    font-size: 40px;
    line-height: 48px;
    letter-spacing: -1px;
  }
</style>
</head>
<body>
<main class="poster">
  <h1 class="quote" aria-label="make every detail perfect and limit the number of details to perfect">
    <span class="quote-line" style="top:163px"><span>make</span><span>every</span></span>
    <span class="quote-line" style="top:258px"><span>d</span><span>e</span><span>t</span><span>a</span><span>i</span><span>l</span></span>
    <span class="quote-line" style="top:352px"><span>p</span><span>e</span><span>r</span><span>f</span><span>e</span><span>c</span><span>t</span></span>
    <span class="quote-line" style="top:447px"><span>and</span><span>limit</span><span>the</span></span>
    <span class="quote-line" style="top:542px"><span>number</span><span>of</span></span>
    <span class="quote-line" style="top:637px"><span>details</span><span>to</span></span>
    <span class="quote-line" style="top:732px"><span>p</span><span>e</span><span>r</span><span>f</span><span>e</span><span>c</span><span>t</span></span>
  </h1>

  <p class="attribution">Milo Hartwell,<br>Co founder of Chirplane</p>

  <p class="brand-name">Brookloft</p>
</main>
</body>
</html>
```